Varentoria Business Card and Letter Head

We are a leadership assessment consultancy based in Sydney, Australia. We help executive-level decison-makers select leaders for more senior level roles in corporate and government organisations. Our methodology is based on the latest research from the field of neuroscience.
We need a business card design and matching letter head that presents our company, Varentoria, as a:
1. trusted adviser to senior executive-level decison makers
2. niche consultancy who are experts in the field of assessing leadership talent
3. results-focused solution provider who balance scientific methods with pragmatic solutions
The following company details should be used in all designs:
Company Name: Varentoria
Details (for business card):
Derek Hanford
Prime Capacity Officer
Level 14, Marlow Tower
7 Marlow Square
Harbourvale, NSW 2099 Australia
Phone: 1300 582 714
Mobile: 0412 637 258
Email: derek.hanford@varentoria-example.com.au
Website: varentoria-example.com.au
I have attached the logo for Varentoria (for both a white and black background) - your business card and letter head designs must incoporate this logo and colour scheme.
Thanks for your interest in this project, I'm looking forward to receiving your ideas.
Regards,
Derek
Target Market(s)
Executive-level decison-makers in corporate and government organisations (e.g., CEO, VP, Head of Human Resources)
Industry/Entity Type
Leadership
Look and feel

```html
<!DOCTYPE html>
<html lang="en">
<head>
<meta charset="utf-8">
<title>Varentoria Business Card</title>
<link href="https://fonts.googleapis.com/css2?family=Open+Sans:wght@400;600;700&display=swap" rel="stylesheet">
<style>
  :root {
    --page-bg: #ece9e4;
    --card-white: #ffffff;
    --charcoal: #434343;
    --ink: #3a3a3a;
    --brand-red: #b8251c;
    --text-grey: #555555;
  }
  * { box-sizing: border-box; margin: 0; padding: 0; }
  html, body {
    width: 1200px; height: 469px; overflow: hidden;
    background: var(--page-bg);
    font-family: "Open Sans", Arial, sans-serif;
  }
  .stage { position: relative; width: 1200px; height: 469px; }
  .card {
    position: absolute; top: 82px;
    width: 526px; height: 302px;
    background: var(--card-white);
    overflow: hidden;
    box-shadow: 0 4px 10px rgba(0,0,0,0.28);
  }
  .card--front { left: 47px; }
  .card--back { left: 615px; }
  .card__swoosh { position: absolute; inset: 0; width: 526px; height: 302px; }
  .brand { position: absolute; display: flex; align-items: center; gap: 12px; }
  .card--front .brand { left: 45px; top: 78px; }
  .card--back .brand { left: 47px; top: 83px; }
  .brand__mark { width: 56px; height: 56px; background: var(--charcoal); }
  .brand__text { display: flex; flex-direction: column; }
  .brand__name {
    font-size: 40px; font-weight: 600; color: var(--charcoal);
    line-height: 1; letter-spacing: -0.5px;
  }
  .brand__tagline {
    margin-top: 6px; font-size: 11.5px; color: var(--text-grey);
    letter-spacing: 0.4px; line-height: 1;
  }
  .address {
    position: absolute; right: 15px; top: 86px;
    text-align: right; font-size: 11.5px; line-height: 17px; color: var(--ink);
    font-style: normal;
  }
  .person { position: absolute; left: 119px; top: 194px; }
  .person__name { font-size: 14px; font-weight: 700; color: var(--brand-red); line-height: 18px; }
  .person__title { font-size: 11px; color: var(--ink); line-height: 13px; }
  .contacts {
    position: absolute; right: 10px; top: 220px;
    list-style: none; text-align: right;
    font-size: 11.5px; line-height: 17px; color: #ffffff;
  }
  .contacts li { display: flex; justify-content: flex-end; align-items: center; gap: 9px; }
  .contacts__icon { width: 9px; height: 9px; border-radius: 50%; background: var(--brand-red); flex: none; }
  .contacts__icon--square { border-radius: 1px; }
  .web-back {
    position: absolute; right: 24px; top: 253px;
    font-size: 13px; color: #ffffff;
  }
</style>
</head>
<body>
<main class="stage">

  <section class="card card--front">
    <svg class="card__swoosh" viewBox="0 0 526 302" aria-hidden="true">
      <defs>
        <linearGradient id="silverFront" x1="0" x2="1" y1="0" y2="0">
          <stop offset="0" stop-color="#ffffff"/>
          <stop offset="1" stop-color="#8a8a8a"/>
        </linearGradient>
      </defs>
      <path d="M0 268 C90 285 190 285 280 248 C360 214 440 170 526 166 L526 302 L0 302 Z" fill="var(--charcoal)"/>
      <path d="M0 250 C70 275 170 292 260 276 C180 298 80 290 0 270 Z" fill="url(#silverFront)"/>
      <path d="M45 252 C150 280 240 272 320 228 C400 184 460 162 526 156 L526 163 C462 170 402 192 324 236 C244 280 150 286 45 252 Z" fill="var(--brand-red)"/>
    </svg>
    <div class="brand">
      <div class="brand__mark"></div>
      <div class="brand__text">
        <span class="brand__name">Varentoria</span>
        <span class="brand__tagline">SELECTING FUTURE EXECUTIVES</span>
      </div>
    </div>
    <address class="address">
      Level 14, Marlow Tower<br>
      7 Marlow Square<br>
      Harbourvale, NSW 2099 Australia
    </address>
    <div class="person">
      <p class="person__name">Derek Hanford</p>
      <p class="person__title">Prime Capacity Officer</p>
    </div>
    <ul class="contacts">
      <li>1300 582 714 <span class="contacts__icon"></span></li>
      <li>0412 637 258 <span class="contacts__icon contacts__icon--square"></span></li>
      <li>derek.hanford@varentoria-example.com.au <span class="contacts__icon contacts__icon--square"></span></li>
      <li>www.varentoria-example.com.au <span class="contacts__icon"></span></li>
    </ul>
  </section>

  <section class="card card--back">
    <svg class="card__swoosh" viewBox="0 0 526 302" aria-hidden="true">
      <defs>
        <linearGradient id="silverBack" x1="0" x2="1" y1="0" y2="0">
          <stop offset="0" stop-color="#ffffff"/>
          <stop offset="1" stop-color="#8a8a8a"/>
        </linearGradient>
      </defs>
      <path d="M0 268 C90 285 190 285 280 248 C360 214 440 170 526 166 L526 302 L0 302 Z" fill="var(--charcoal)"/>
      <path d="M0 250 C70 275 170 292 260 276 C180 298 80 290 0 270 Z" fill="url(#silverBack)"/>
      <path d="M45 252 C150 280 240 272 320 228 C400 184 460 162 526 156 L526 163 C462 170 402 192 324 236 C244 280 150 286 45 252 Z" fill="var(--brand-red)"/>
    </svg>
    <div class="brand">
      <div class="brand__mark"></div>
      <div class="brand__text">
        <span class="brand__name">Varentoria</span>
        <span class="brand__tagline">SELECTING FUTURE EXECUTIVES</span>
      </div>
    </div>
    <p class="web-back">www.varentoria-example.com.au</p>
  </section>

</main>
</body>
</html>
```